Web Developer Needs a Business Card Design

I need a personal business card design that represents me as a web developer for potential employers. I would like the background to be a dark color on the front for contrast with my logo and name. The back will have all my information along with a smaller version of the logo. I want something with a modern look and feel, not too conservative. This will be used for potential employers and freelance work.

Industry/Entity Type

Business

Contact Information for Business Card

Front should have my logo and name. The back should have all my personal information which would include: name: Tom Varulek, phone: 570-614-3098, email: tomvarulek@quillbox.net, website url: www.tomvarulek.net, logo, web developer.

Font styles to use
Sans Serif

Requirements
Must have
• Must include my logo. The color palette base color will be the logo color.

```html
<!DOCTYPE html>
<html lang="en">
<head>
<meta charset="utf-8">
<title>Tom Varulek – Business Card</title>
<link href="https://fonts.googleapis.com/css2?family=Source+Sans+3:wght@400;500&display=swap" rel="stylesheet">
<style>
  :root {
    --page: #d9d9d9;
    --teal: #5fb9a3;
    --teal-bright: #3ec7a2;
    --teal-edge: #56a792;
    --ink: #111111;
    --ink-light: #f2f2f2;
    --paper-light: #ffffff;
    --paper-shade: #d2d2d2;
    --dark-light: #3a3f3e;
    --dark-shade: #1c1f1f;
  }
  * { box-sizing: border-box; margin: 0; padding: 0; }
  html, body {
    width: 1189px; height: 1200px; overflow: hidden;
    background: var(--page);
    font-family: "Source Sans 3", "Myriad Pro", sans-serif;
  }
  .card {
    position: absolute; left: 140px; width: 917px; height: 524px;
    background: radial-gradient(ellipse at 55% 85%, var(--paper-light) 0%, #f2f2f2 40%, var(--paper-shade) 100%);
    box-shadow: 0 6px 14px rgba(0,0,0,.35);
  }
  .card::before, .card::after {
    content: ""; position: absolute; top: 0; bottom: 0; width: 18px; background: var(--teal-edge);
  }
  .card::before { left: 0; }
  .card::after { right: 0; }
  .card--front {
    top: 45px;
    background: radial-gradient(ellipse at 55% 85%, var(--dark-light) 0%, #2b2f2f 45%, var(--dark-shade) 100%);
  }
  .card--back { top: 623px; }

  .brand-mark {
    position: absolute; width: 326px; height: 326px; border-radius: 50%;
    border: 12px solid var(--teal);
    display: flex; align-items: center; justify-content: center;
  }
  .brand-mark__name {
    color: var(--teal); font-size: 40px; font-weight: 500; letter-spacing: .5px;
  }
  .card--front .brand-mark { left: 78px; top: 49px; }
  .card--back .brand-mark { left: 298px; top: 59px; }

  .identity { position: absolute; right: 78px; top: 268px; text-align: right; }
  .identity__name { color: var(--teal-bright); font-size: 62px; font-weight: 400; line-height: 1; }
  .identity__role { color: var(--ink-light); font-size: 30px; line-height: 1.1; margin-top: 2px; }

  .contacts { position: absolute; right: 77px; top: 385px; list-style: none; }
  .contacts li {
    display: flex; align-items: center; justify-content: flex-end;
    font-size: 26px; color: var(--ink-light); height: 35px; gap: 20px;
  }
  .contacts svg { width: 21px; height: 21px; flex: none; }

  .back-name {
    position: absolute; left: 0; right: 0; top: 392px; text-align: center;
    font-size: 70px; font-weight: 400; color: var(--ink);
  }
</style>
</head>
<body>
  <section class="card card--front">
    <div class="brand-mark"><span class="brand-mark__name">Tom Varulek</span></div>
    <div class="identity">
      <h1 class="identity__name">Tom Varulek</h1>
      <p class="identity__role">web developer</p>
    </div>
    <ul class="contacts">
      <li>570-614-3098
        <svg viewBox="0 0 20 20" aria-hidden="true"><rect width="20" height="20" fill="#f2f2f2"/><path d="M6 3.5l2.5 3-1.5 1.5c.8 2 2.2 3.4 4 4.3l1.5-1.5 3 2.5-1.5 2.5c-4.5-.5-8.5-4.5-9.5-9.5z" fill="#1c1f1f"/></svg>
      </li>
      <li>www.tomvarulek.net
        <svg viewBox="0 0 20 20" aria-hidden="true"><rect width="20" height="20" fill="#f2f2f2"/><circle cx="10" cy="10" r="6.5" fill="none" stroke="#1c1f1f" stroke-width="1.5"/><path d="M3.5 10h13M10 3.5c-3 3.5-3 9.5 0 13M10 3.5c3 3.5 3 9.5 0 13" fill="none" stroke="#1c1f1f" stroke-width="1.2"/></svg>
      </li>
      <li>tomvarulek@quillbox.net
        <svg viewBox="0 0 20 20" aria-hidden="true"><rect width="20" height="20" fill="#f2f2f2"/><rect x="3.5" y="5.5" width="13" height="9" fill="none" stroke="#1c1f1f" stroke-width="1.4"/><path d="M3.5 5.5l6.5 5 6.5-5" fill="none" stroke="#1c1f1f" stroke-width="1.4"/></svg>
      </li>
    </ul>
  </section>

  <section class="card card--back">
    <div class="brand-mark"><span class="brand-mark__name">Tom Varulek</span></div>
    <p class="back-name">Tom Varulek</p>
  </section>
</body>
</html>
```